We need a business card design for a new company located in Missouri City, TX, entitled 'BrightPath Chiropractic & Holistic Center'. Our services include restoration of health and vitality, spinal exam, health assessment, dietary & fitness programs, lymphatic & therapeutic massage, detox & remineralize body wraps, far infrared sauna therapy

Industry/Entity Type

Business

Contact Information for Business Card

BrightPath Chiropractic & Holistic Center, Marlene Okafor LMT, 4215 Elm Ridge Rd., Suite 310, Missouri City, TX 77482, 281-555-0193

```html
<!DOCTYPE html>
<html lang="en">
<head>
<meta charset="utf-8">
<title>BrightPath Chiropractic &amp; Holistic Center – Business Card</title>
<link rel="stylesheet" href="https://fonts.googleapis.com/css2?family=Open+Sans:wght@400;600;700&family=Questrial&family=Libre+Baskerville&display=swap">
<style>
  :root {
    --teal: #1fa88f;
    --ink: #141414;
    --band: #121212;
    --paper: #ffffff;
    --name-blue: #2f73ad;
    --backdrop: #e7e5e1;
    --faint: rgba(31, 168, 143, 0.16);
    --list-ink: #1a1a1a;
  }
  * { box-sizing: border-box; margin: 0; padding: 0; }
  html, body { width: 1200px; height: 892px; overflow: hidden; background: var(--backdrop); }
  .canvas { position: relative; width: 1200px; height: 892px; }

  .card {
    position: absolute; left: 270px; width: 660px; height: 377px;
    background: var(--paper); overflow: hidden;
    box-shadow: 0 6px 18px rgba(0,0,0,0.18);
    font-family: "Open Sans", sans-serif;
  }
  .card--front { top: 48px; }
  .card--back { top: 467px; }

  .card__bands { position: absolute; inset: 0; }

  .brand-title {
    position: absolute; right: 28px; top: 14px; text-align: right;
    color: var(--paper); font-weight: 700; line-height: 1.15;
  }
  .brand-title__main { font-size: 30px; display: block; }
  .brand-title__sub { font-size: 22px; display: block; }

  .holder { position: absolute; left: 40px; top: 70px; }
  .holder__name { color: var(--name-blue); font-weight: 600; font-size: 24px; }
  .holder__role { color: var(--ink); font-weight: 700; font-size: 13px; }

  .brand-mark {
    position: absolute; right: 70px; top: 170px;
    display: flex; align-items: center; gap: 10px;
    color: var(--teal); font-weight: 700; font-size: 26px;
  }
  .brand-mark__dot { width: 22px; height: 22px; border-radius: 50%; background: var(--teal); }

  .contact { position: absolute; color: var(--paper); font-weight: 600; font-size: 12.5px; line-height: 1.55; }
  .contact--personal { left: 24px; top: 268px; }
  .contact--office { left: 254px; top: 318px; }
  .contact__row { display: flex; align-items: center; gap: 8px; white-space: nowrap; }
  .contact__row--plain { padding-left: 24px; }
  .contact__icon { width: 16px; height: 16px; flex: none; }
  .contact-divider { position: absolute; left: 240px; top: 272px; width: 1px; height: 90px; background: rgba(255,255,255,0.55); }

  .services-title {
    position: absolute; left: 62px; top: 30px;
    font-family: "Libre Baskerville", serif; font-size: 46px; color: var(--ink);
  }
  .services-list {
    position: absolute; left: 62px; top: 118px; list-style: none;
    font-family: "Questrial", sans-serif; font-size: 21px; color: var(--list-ink); line-height: 1.52;
  }
  .services-list li::before { content: "*"; color: var(--teal); font-weight: 700; margin-right: 12px; font-family: "Open Sans", sans-serif; }

  .faint-mark {
    position: absolute; right: 30px; bottom: 40px;
    display: flex; align-items: center; gap: 10px;
    font-family: "Open Sans", sans-serif; font-weight: 700; font-size: 30px; color: var(--faint);
  }
  .faint-mark__dot { width: 28px; height: 28px; border-radius: 50%; background: var(--faint); }
</style>
</head>
<body>
<main class="canvas">

  <section class="card card--front" aria-label="Business card front">
    <svg class="card__bands" width="660" height="377" viewBox="0 0 660 377" aria-hidden="true">
      <defs>
        <linearGradient id="tealBand" x1="0" y1="0" x2="1" y2="1">
          <stop offset="0" stop-color="#2dbaa0"/>
          <stop offset="1" stop-color="#179a83"/>
        </linearGradient>
      </defs>
      <path d="M150,0 H660 V150 Q420,120 150,0 Z" fill="url(#tealBand)"/>
      <path d="M0,240 Q260,250 660,318 V377 H0 Z" fill="var(--band)"/>
    </svg>

    <h1 class="brand-title">
      <span class="brand-title__main">BrightPath</span>
      <span class="brand-title__sub">Chiropractic&amp;Holistic Center</span>
    </h1>

    <div class="holder">
      <p class="holder__name">Daniel Reyes</p>
      <p class="holder__role">CEO</p>
    </div>

    <div class="brand-mark">
      <span class="brand-mark__dot"></span>
      <span>BrightPath</span>
    </div>

    <div class="contact contact--personal">
      <p class="contact__row">
        <svg class="contact__icon" viewBox="0 0 16 16" aria-hidden="true"><rect width="16" height="16" rx="2" fill="#fff"/><path d="M5 3.5l2 2-1 1.2c.6 1.3 1.6 2.3 2.9 2.9l1.2-1 2 2-1.3 1.6C7.6 12 4 8.4 3.8 4.8z" fill="#2f73ad"/></svg>
        281-555-0193
      </p>
      <p class="contact__row">
        <svg class="contact__icon" viewBox="0 0 16 16" aria-hidden="true"><rect width="16" height="16" rx="2" fill="#fff"/><rect x="3" y="4.5" width="10" height="7" fill="none" stroke="#2f73ad" stroke-width="1.2"/><path d="M3 4.5l5 4 5-4" fill="none" stroke="#2f73ad" stroke-width="1.2"/></svg>
        daniel@brightpathmail.com
      </p>
    </div>

    <span class="contact-divider"></span>

    <div class="contact contact--office">
      <p class="contact__row">
        <svg class="contact__icon" viewBox="0 0 16 16" aria-hidden="true"><rect width="16" height="16" rx="2" fill="#fff"/><circle cx="8" cy="8" r="4.5" fill="none" stroke="#2f73ad" stroke-width="1.2"/><path d="M3.5 8h9M8 3.5c-2 2.5-2 6.5 0 9M8 3.5c2 2.5 2 6.5 0 9" fill="none" stroke="#2f73ad" stroke-width="1"/></svg>
        www.brightpathcenter.com
      </p>
      <p class="contact__row">
        <svg class="contact__icon" viewBox="0 0 16 16" aria-hidden="true"><rect width="16" height="16" rx="2" fill="#fff"/><path d="M8 13s-4-4-4-7a4 4 0 018 0c0 3-4 7-4 7z" fill="#2f73ad"/><circle cx="8" cy="6" r="1.5" fill="#fff"/></svg>
        Marlene Okafor LMT, 4215 Elm Ridge Rd., Suite 310
      </p>
      <p class="contact__row contact__row--plain">Missouri City, TX 77482.</p>
    </div>
  </section>

  <section class="card card--back" aria-label="Business card back">
    <div class="faint-mark" aria-hidden="true">
      <span class="faint-mark__dot"></span>
      <span>BrightPath</span>
    </div>
    <h2 class="services-title">services</h2>
    <ul class="services-list">
      <li>spinal exam</li>
      <li>health assessment</li>
      <li>dietary &amp; fitness programs</li>
      <li>far infrared sauna therapy</li>
      <li>restoration of health and vitality</li>
      <li>detox &amp; remineralize body wraps</li>
      <li>lymphatic &amp; therapeutic massage</li>
    </ul>
  </section>

</main>
</body>
</html>
```